Business Card Design Project - del varosi group

dear Sirs

we need business card design for our group ( DEL Varosi Group ) , i have got the Logo design of our group from pixel harbor in previous , so all need details relating to our group i think available with you, as well as the the chosen logo design

we hope to provide us with business card logo that to be appropaite and satisfactory to us .

thanks

note : logo design of our group is attached .
Updates

Reason: please extend the deadline of my project for additional 15 days because i didn't received appropriate design for our gruop yet . kindly beaware that i have received 77 design till now , supossed to send me 200-250 design at least . thanks

Target Market(s)

contents

name : Kerem EL Nadiri

position : Operation Manager

Industry/Entity Type

Business

Requirements
Must have

• person name

group logo
Nice to have
• logo color matching with back background

```html
<!DOCTYPE html>
<html lang="en">
<head>
<meta charset="utf-8">
<title>DEL Varosi Group – Business Card</title>
<link href="https://fonts.googleapis.com/css2?family=Open+Sans:wght@400;600;700&display=swap" rel="stylesheet">
<style>
  :root {
    --backdrop: #a9862a;
    --card-white: #ffffff;
    --card-grey: #eeeeee;
    --brand-blue: #0c4f93;
    --band-blue-dark: #0b4d8f;
    --band-blue-light: #2f86c6;
    --icon-blue: #1a6fb6;
    --gold-light: #f3c123;
    --gold-dark: #d9963a;
    --ink: #1b1b1b;
  }
  * { box-sizing: border-box; margin: 0; padding: 0; }
  html, body {
    width: 1200px; height: 686px; overflow: hidden;
    background: var(--backdrop);
    font-family: "Open Sans", Arial, sans-serif;
  }
  .stage { position: relative; width: 1200px; height: 686px; }
  .card {
    position: absolute; width: 525px; height: 300px;
    box-shadow: 2px 3px 5px rgba(0,0,0,.35);
    overflow: hidden;
  }
  .card--front {
    left: 60px; top: 146px;
    background: radial-gradient(ellipse at 50% 40%, var(--card-white) 30%, var(--card-grey) 100%);
  }
  .card--back { left: 621px; top: 244px; background: var(--card-white); }

  .wordmark {
    position: absolute; left: 0; right: 0;
    display: flex; align-items: center; justify-content: center; gap: 10px;
    color: var(--brand-blue); font-weight: 600; letter-spacing: .5px;
  }
  .wordmark__square { width: 18px; height: 18px; background: var(--brand-blue); }
  .card--front .wordmark { top: 70px; font-size: 34px; }
  .card--back .wordmark { top: 156px; font-size: 36px; }

  .contact {
    position: absolute; left: 0; right: 0; top: 160px;
    text-align: center; color: var(--ink); font-size: 12.5px; line-height: 19px;
  }
  .contact__row { display: flex; justify-content: center; gap: 16px; }
  .contact__item { display: inline-flex; align-items: center; gap: 3px; }
  .contact__item svg { width: 11px; height: 11px; fill: var(--icon-blue); }

  .name-band {
    position: absolute; left: 0; right: 0; bottom: 0; height: 51px;
    background: linear-gradient(90deg, var(--band-blue-dark), var(--band-blue-light) 50%, var(--band-blue-dark));
    display: flex; align-items: center; justify-content: center;
    color: var(--card-white);
  }
  .name-band__name { font-weight: 700; font-size: 14.5px; }
  .name-band__divider { width: 1px; height: 14px; background: var(--card-white); margin: 0 9px; }
  .name-band__role { font-weight: 600; font-size: 12.5px; }

  .web-band {
    position: absolute; left: 0; right: 0; top: 0; height: 51px;
    background: linear-gradient(90deg, var(--gold-dark), var(--gold-light) 50%, var(--gold-dark));
    display: flex; align-items: center; justify-content: center;
    color: var(--card-white); font-weight: 700; font-size: 12px; letter-spacing: 1.5px;
  }
</style>
</head>
<body>
<div class="stage">

  <section class="card card--front">
    <div class="wordmark"><span class="wordmark__square"></span>DEL Varosi Group</div>

    <div class="contact">
      <div class="contact__row">
        <span class="contact__item"><svg viewBox="0 0 24 24"><path d="M6.6 10.8a15 15 0 006.6 6.6l2.2-2.2c.3-.3.7-.4 1-.2 1.1.4 2.3.6 3.6.6.6 0 1 .4 1 1V20c0 .6-.4 1-1 1A17 17 0 013 4c0-.6.4-1 1-1h3.5c.6 0 1 .4 1 1 0 1.3.2 2.5.6 3.6.1.3 0 .7-.2 1z"/></svg>(TF)123-456-7890</span>
        <span class="contact__item"><svg viewBox="0 0 24 24"><path d="M6.6 10.8a15 15 0 006.6 6.6l2.2-2.2c.3-.3.7-.4 1-.2 1.1.4 2.3.6 3.6.6.6 0 1 .4 1 1V20c0 .6-.4 1-1 1A17 17 0 013 4c0-.6.4-1 1-1h3.5c.6 0 1 .4 1 1 0 1.3.2 2.5.6 3.6.1.3 0 .7-.2 1z"/></svg>123-456-7890</span>
        <span class="contact__item"><svg viewBox="0 0 24 24"><path d="M6 2h12v6H6zM3 9h18v9h-3v4H6v-4H3zm5 6v5h8v-5z"/></svg>123-456-7890</span>
      </div>
      <div class="contact__row">
        <span class="contact__item"><svg viewBox="0 0 24 24"><path d="M2 5h20v14H2zm2 2v.5l8 5 8-5V7z"/></svg>name@website.com</span>
        <span class="contact__item"><svg viewBox="0 0 24 24"><path d="M12 2a10 10 0 100 20 10 10 0 000-20zm6.9 6h-3a15 15 0 00-1.3-4A8 8 0 0118.9 8zM12 4c.8 1.1 1.5 2.5 1.9 4h-3.8c.4-1.5 1.1-2.9 1.9-4zM4.3 14a8 8 0 010-4h3.4a16 16 0 000 4zm.8 2h3a15 15 0 001.3 4A8 8 0 015.1 16zm3-8h-3a8 8 0 014.3-4 15 15 0 00-1.3 4zM12 20c-.8-1.1-1.5-2.5-1.9-4h3.8c-.4 1.5-1.1 2.9-1.9 4zm2.3-6H9.7a14 14 0 010-4h4.6a14 14 0 010 4zm.3 6a15 15 0 001.3-4h3a8 8 0 01-4.3 4zm1.7-6a16 16 0 000-4h3.4a8 8 0 010 4z"/></svg>www.website.com</span>
      </div>
      <div class="contact__row">Street name City, State, zip code</div>
    </div>

    <div class="name-band">
      <span class="name-band__name">Kerem EL Nadiri</span>
      <span class="name-band__divider"></span>
      <span class="name-band__role">Operation Manager</span>
    </div>
  </section>

  <section class="card card--back">
    <div class="web-band">www.website.com</div>
    <div class="wordmark"><span class="wordmark__square"></span>DEL Varosi Group</div>
  </section>

</div>
</body>
</html>
```